Redesign of business card for Cedar Ridge Mechanical

We are looking for a new design for our business cards for Cedar Ridge Mechanical. We are a plumbing & HVAC construction company, operating on the West Coast of Canada and USA. Logo attached.
Industry/Entity Type
Construction - Plumbing & HVAC
Contact Information for Business Card
Name, address, phone numbers, email, website address
Look and feel
Each slider illustrates characteristics of the customer's brand and the style your logo design should communicate.

```html
<!DOCTYPE html>
<html lang="en">
<head>
<meta charset="utf-8">
<title>Cedar Ridge Mechanical – Business Card</title>
<link rel="stylesheet" href="https://fonts.googleapis.com/css2?family=Montserrat:wght@400;500;700;800&display=swap">
<style>
  :root {
    --ink: #111111;
    --paper: #ffffff;
    --backdrop: #e4e4e4;
    --silver: #a8a8a8;
    --muted: #333333;
  }
  * { margin: 0; padding: 0; box-sizing: border-box; }
  html, body { width: 1200px; height: 913px; overflow: hidden; }
  body {
    background: var(--backdrop);
    font-family: "Montserrat", sans-serif;
    color: var(--ink);
    position: relative;
  }
  .card {
    position: absolute;
    left: 250px;
    width: 700px;
    height: 400px;
    background: var(--paper);
    border-radius: 28px;
    overflow: hidden;
    box-shadow: 0 6px 18px rgba(0,0,0,0.18);
  }
  .card--front { top: 40px; }
  .card--back { top: 473px; }

  .brand {
    position: absolute;
    display: flex;
    align-items: center;
    gap: 16px;
    font-weight: 800;
    text-transform: uppercase;
    color: var(--ink);
    white-space: nowrap;
  }
  .brand__mark { background: var(--ink); flex: none; }
  .card--front .brand {
    left: 0; right: 0; top: 0; bottom: 0;
    justify-content: center;
    font-size: 38px;
    letter-spacing: 1px;
  }
  .card--front .brand__mark { width: 42px; height: 42px; }
  .card--back .brand {
    left: 290px; top: 60px;
    font-size: 22px;
    gap: 10px;
  }
  .card--back .brand__mark { width: 24px; height: 24px; }

  .swoosh { position: absolute; inset: 0; }

  .person { position: absolute; left: 62px; top: 222px; }
  .person__name { font-size: 28px; font-weight: 800; letter-spacing: 1px; }
  .person__role { font-size: 18px; font-weight: 400; color: var(--muted); margin-top: 2px; }

  .divider {
    position: absolute;
    left: 345px; top: 140px;
    width: 1px; height: 100px;
    background: var(--ink);
  }

  .contacts {
    position: absolute;
    left: 372px; top: 140px;
    list-style: none;
    font-size: 17px;
    line-height: 27px;
  }
  .contacts li { display: flex; align-items: center; gap: 8px; }
  .contacts svg { width: 15px; height: 15px; flex: none; }

  .address {
    position: absolute;
    right: 40px; top: 358px;
    color: var(--paper);
    font-size: 17px;
    font-weight: 400;
  }
</style>
</head>
<body>
  <section class="card card--front" aria-label="Card front">
    <div class="brand"><span class="brand__mark"></span>Cedar Ridge Mechanical</div>
  </section>

  <section class="card card--back" aria-label="Card back">
    <svg class="swoosh" viewBox="0 0 700 400" width="700" height="400" aria-hidden="true">
      <path d="M0,338 Q470,326 700,182" fill="none" stroke="var(--silver)" stroke-width="6"/>
      <path d="M0,355 Q480,340 700,200 L700,400 L0,400 Z" fill="var(--ink)"/>
    </svg>

    <div class="brand"><span class="brand__mark"></span>Cedar Ridge Mechanical</div>

    <div class="person">
      <div class="person__name">DANIEL HAYES</div>
      <div class="person__role">Managing Director</div>
    </div>

    <div class="divider"></div>

    <ul class="contacts">
      <li>
        <svg viewBox="0 0 16 16" aria-hidden="true"><circle cx="8" cy="8" r="8" fill="var(--ink)"/><path d="M5 4.5l1.6-.4 1 2-1 .8a5 5 0 0 0 2.5 2.5l.8-1 2 1-.4 1.6c-3.5.3-6.8-3-6.5-6.5z" fill="var(--paper)"/></svg>
        123 456 789
      </li>
      <li>
        <svg viewBox="0 0 16 16" aria-hidden="true"><rect x="1" y="3" width="14" height="10" rx="1.5" fill="var(--ink)"/><path d="M2 4.5l6 4.5 6-4.5" fill="none" stroke="var(--paper)" stroke-width="1.3"/></svg>
        info@yourgmail.com
      </li>
      <li>
        <svg viewBox="0 0 16 16" aria-hidden="true"><circle cx="8" cy="8" r="7" fill="var(--ink)"/><path d="M1 8h14M8 1c-3 3.5-3 10.5 0 14M8 1c3 3.5 3 10.5 0 14" fill="none" stroke="var(--paper)" stroke-width="1"/></svg>
        www.yourwebsite.com
      </li>
    </ul>

    <div class="address">Your address, City State, Zip 1234</div>
  </section>
</body>
</html>
```